TA BRAMLEY BUSINESS CARD DESIGN PROJECT

We need to utilize our logo that was expertly created on PixelHarbor and now need to match this with a business card design.

```html
<!DOCTYPE html>
<html lang="en">
<head>
<meta charset="utf-8">
<title>TA Bramley – Business Card</title>
<link rel="stylesheet" href="https://fonts.googleapis.com/css2?family=Montserrat:wght@400;500;700&display=swap">
<style>
  :root {
    --brand-blue: #1456ad;
    --card-white: #ffffff;
    --card-black: #161616;
    --stage-grey: #d9dadc;
    --text-light: #f2f2f2;
  }
  * { box-sizing: border-box; margin: 0; padding: 0; }
  html, body {
    width: 1200px;
    height: 900px;
    overflow: hidden;
    background: var(--stage-grey);
    font-family: "Montserrat", sans-serif;
  }
  .canvas {
    position: relative;
    width: 1200px;
    height: 900px;
  }
  .card {
    position: absolute;
    left: 250px;
    width: 700px;
    height: 400px;
    border-radius: 26px;
    overflow: hidden;
    background: var(--card-white);
    box-shadow: 0 6px 18px rgba(0,0,0,0.18);
  }
  .card--front { top: 40px; }
  .card--back  { top: 460px; }

  .brand-name {
    display: flex;
    align-items: center;
    gap: 18px;
    color: var(--brand-blue);
    font-weight: 700;
    letter-spacing: 0.12em;
    white-space: nowrap;
  }
  .brand-name__dot {
    display: block;
    border-radius: 50%;
    background: var(--brand-blue);
  }
  .card--front .brand-name {
    position: absolute;
    inset: 0;
    justify-content: center;
    font-size: 64px;
  }
  .card--front .brand-name__dot { width: 44px; height: 44px; }

  .card--back .brand-name {
    position: absolute;
    top: 60px;
    right: 40px;
    font-size: 34px;
    gap: 12px;
  }
  .card--back .brand-name__dot { width: 24px; height: 24px; }

  .back-wave {
    position: absolute;
    inset: 0;
    width: 700px;
    height: 400px;
  }

  .contact {
    position: absolute;
    left: 60px;
    top: 200px;
    color: var(--text-light);
  }
  .contact__accent {
    position: absolute;
    left: -24px;
    top: 4px;
    width: 12px;
    height: 50px;
    background: var(--brand-blue);
  }
  .contact__name {
    color: var(--brand-blue);
    font-weight: 700;
    font-size: 24px;
    letter-spacing: 0.03em;
  }
  .contact__role {
    font-size: 17px;
    margin-top: 2px;
  }
  .contact__address {
    font-size: 16px;
    line-height: 1.35;
    margin-top: 16px;
  }
  .contact__list {
    list-style: none;
    margin-top: 14px;
    font-size: 16px;
    line-height: 1.5;
  }
  .contact__list li {
    display: flex;
    align-items: center;
    gap: 10px;
  }
  .contact__icon { width: 14px; height: 14px; flex: none; }
</style>
</head>
<body>
<main class="canvas">

  <section class="card card--front" aria-label="Business card front">
    <div class="brand-name">
      <span class="brand-name__dot"></span>
      <span>TA BRAMLEY</span>
    </div>
  </section>

  <section class="card card--back" aria-label="Business card back">
    <svg class="back-wave" viewBox="0 0 700 400" aria-hidden="true">
      <path d="M0,150 C180,100 380,250 700,205 L700,400 L0,400 Z" fill="var(--brand-blue)"/>
      <path d="M0,168 C190,118 390,266 700,224 L700,400 L0,400 Z" fill="var(--card-white)"/>
      <path d="M0,176 C190,126 390,274 700,232 L700,400 L0,400 Z" fill="var(--card-black)"/>
      <path d="M0,128 C180,86 380,236 700,190" fill="none" stroke="var(--brand-blue)" stroke-width="2.5"/>
    </svg>

    <div class="brand-name">
      <span class="brand-name__dot"></span>
      <span>TA BRAMLEY</span>
    </div>

    <div class="contact">
      <span class="contact__accent"></span>
      <p class="contact__name">OWEN HARTLEY</p>
      <p class="contact__role">Managing Director</p>
      <p class="contact__address">Your address, City<br>State, Zip 1234</p>
      <ul class="contact__list">
        <li>
          <svg class="contact__icon" viewBox="0 0 16 16"><path d="M3 1h3l1.5 4-2 1.3a9 9 0 0 0 4.2 4.2L11 8.5l4 1.5v3a2 2 0 0 1-2 2C6.4 15 1 9.6 1 3a2 2 0 0 1 2-2z" fill="var(--brand-blue)"/></svg>
          123 456 789
        </li>
        <li>
          <svg class="contact__icon" viewBox="0 0 16 16"><rect x="1" y="3" width="14" height="10" rx="1" fill="var(--brand-blue)"/><path d="M1.5 4 8 9l6.5-5" fill="none" stroke="var(--card-black)" stroke-width="1.3"/></svg>
          info@yourmail.com
        </li>
        <li>
          <svg class="contact__icon" viewBox="0 0 16 16"><circle cx="8" cy="8" r="7" fill="var(--brand-blue)"/><path d="M1 8h14M8 1c-3 3.5-3 10.5 0 14M8 1c3 3.5 3 10.5 0 14" fill="none" stroke="var(--card-black)" stroke-width="1"/></svg>
          www.yourwebsite.com
        </li>
      </ul>
    </div>
  </section>

</main>
</body>
</html>
```